Local Flower Farm Needs Business Card Design

I need business cards designed for a flower farm based in Eudora, Kansas.
Business Info:
We are a local cut flower farm located in Eudora, Kansas, founded by Corinne Haldwick. What started as a passion for agriculture and search for more joy in daily life has blossomed into a small business dedicated to providing the community with beautiful, fresh, and sustainable flowers. We specialize in local, seasonal blooms, ensuring that every petal reflects the care and dedication we pour into our craft. Our mission is to deliver the highest quality flowers directly to our customers through local farmers markets and to florists who share our commitment to sustainability. Join us in celebrating the beauty of nature, one bloom at a time!
Contact Details:
Corinne Haldwick
Owner
Phone 913-555-0147
Facebook: Rosalind Thorpe Gardens
Instagram: @RosalindThorpeGardens
Website: RosalindThorpeGardens.example
Target Market(s)
Wholesale to Florists and Direct to Consumer via Farmers Market
Industry/Entity Type
Florist, Farm
Contact Information for Business Card
Name, Contact Info, Logo
Look and feel
Each slider illustrates characteristics of the customer's brand and the style your logo design should communicate.

```html
<!DOCTYPE html>
<html lang="en">
<head>
<meta charset="utf-8">
<title>Rosalind Thorpe Gardens – Business Card</title>
<link rel="stylesheet" href="https://fonts.googleapis.com/css2?family=EB+Garamond:wght@400;700&display=swap">
<style>
  :root {
    --ink: #0b282c;
    --paper: #ffffff;
    --mist: #c3c8cc;
    --backdrop: #d9dadb;
    --shadow: rgba(0,0,0,0.18);
  }
  html, body {
    margin: 0;
    width: 1200px;
    height: 900px;
    overflow: hidden;
    background: var(--backdrop);
  }
  .canvas {
    width: 1200px;
    height: 900px;
    display: flex;
    flex-direction: column;
    align-items: center;
    justify-content: center;
    gap: 44px;
  }
  .card {
    width: 665px;
    height: 380px;
    display: block;
    box-shadow: 0 8px 24px var(--shadow);
    font-family: "EB Garamond", Georgia, serif;
  }
  .brand-ring { fill: none; stroke-width: 1.4; }
  .brand-rule { stroke-width: 1; }
  .brand-name { font-weight: 400; letter-spacing: 3px; text-anchor: middle; }
  .front .brand-ring, .front .brand-rule { stroke: var(--paper); }
  .front .brand-name { fill: var(--paper); }
  .back .brand-ring, .back .brand-rule { stroke: var(--ink); }
  .back .brand-name { fill: var(--ink); }
  .contact text { fill: var(--paper); text-anchor: end; font-size: 17px; }
  .contact .person { font-size: 24px; font-weight: 700; }
  .contact .role { font-size: 15px; }
  .icon { fill: var(--paper); }
  .icon-line { fill: none; stroke: var(--ink); stroke-width: 1.3; }
  .icon-glyph { fill: var(--ink); font-size: 12px; font-weight: 700; text-anchor: middle; }
</style>
</head>
<body>
<main class="canvas">

  <svg class="card front" viewBox="0 0 665 380" role="group" aria-label="Card front">
    <rect width="665" height="380" fill="var(--ink)"/>
    <g class="brand">
      <circle class="brand-ring" cx="332" cy="190" r="118"/>
      <text class="brand-name" x="332" y="166" font-size="30">ROSALIND</text>
      <text class="brand-name" x="332" y="202" font-size="30">THORPE</text>
      <line class="brand-rule" x1="292" y1="218" x2="372" y2="218"/>
      <text class="brand-name" x="332" y="244" font-size="17">GARDENS</text>
    </g>
  </svg>

  <svg class="card back" viewBox="0 0 665 380" role="group" aria-label="Card back">
    <rect width="665" height="380" fill="var(--paper)"/>
    <g class="wave">
      <path d="M0,335 C230,335 330,295 420,175 C490,85 560,64 665,58 L665,380 L0,380 Z" fill="var(--ink)"/>
      <path d="M0,335 C230,335 330,295 420,175 C490,85 560,64 665,58" fill="none" stroke="var(--mist)" stroke-width="10" transform="translate(0,-14)"/>
      <path d="M0,335 C230,335 330,295 420,175 C490,85 560,64 665,58" fill="none" stroke="var(--ink)" stroke-width="5" transform="translate(0,-30)"/>
    </g>

    <g class="brand">
      <circle class="brand-ring" cx="150" cy="160" r="96"/>
      <text class="brand-name" x="150" y="141" font-size="24">ROSALIND</text>
      <text class="brand-name" x="150" y="170" font-size="24">THORPE</text>
      <line class="brand-rule" x1="118" y1="183" x2="182" y2="183"/>
      <text class="brand-name" x="150" y="204" font-size="14">GARDENS</text>
    </g>

    <g class="contact">
      <text class="person" x="625" y="182">Corinne Haldwick</text>
      <text class="role" x="625" y="202">Owner</text>

      <text x="598" y="248">913-555-0147</text>
      <text x="598" y="272">RosalindThorpeGardens.example</text>
      <text x="598" y="296">Rosalind Thorpe Gardens</text>
      <text x="598" y="320">@RosalindThorpeGardens</text>

      <g class="icon-phone" transform="translate(606,236)">
        <rect class="icon" width="16" height="16" rx="3"/>
        <path class="icon-line" d="M4,5 C4,3 6,3 8,3 C10,3 12,3 12,5 M5,7 L11,7 L12,13 L4,13 Z"/>
      </g>
      <g class="icon-globe" transform="translate(606,260)">
        <circle class="icon" cx="8" cy="8" r="8"/>
        <ellipse class="icon-line" cx="8" cy="8" rx="3.5" ry="7"/>
        <path class="icon-line" d="M1,8 L15,8"/>
      </g>
      <g class="icon-page" transform="translate(606,284)">
        <rect class="icon" width="16" height="16" rx="3"/>
        <path class="icon-line" d="M4,4.5 L12,4.5 L12,10 L7,10 L4.5,12.5 L4.5,10 L4,10 Z"/>
      </g>
      <g class="icon-handle" transform="translate(606,308)">
        <rect class="icon" width="16" height="16" rx="3"/>
        <text class="icon-glyph" x="8" y="12.5">@</text>
      </g>
    </g>
  </svg>

</main>
</body>
</html>
```